COMPANY NAME: Bright Harbor Ventures: Task Description: We are a new UK based business with global rea

Target Market

- Personal and professional development – 30-55 age group, corporate leaders, Eastern European and Asian markets
- On-assignment projects – Corporate market – Eastern European and Asian Markets
- Property investment - 35-65 age group, Europe, USA, Australia

What we need

We need logos and brand design for a suite of web platforms (website, twitter and Facebook profile). We would like to have a cohesive and consistent look across all of our online platforms. The design suite must therefore include social media logos, backgrounds and headers. Specifically we are looking for:

a. Facebook header/page design: likely to have a more youthful look

b. Website: Header, background and layout that is responsive to devices, iPhone primarily, then tablet, then PC (we have purchased a website building package from SiteKettle so if you are familiar with one of their themes, it would be great to have a design that fits with a theme you would recommend); Design should be able to accommodate a place to position video in the medium term but an image in the short term.

c. LinkedIn: header/logo; more corporate look

d. Twitter: background/logo

e. Powerpoint template: background and logo - simple and soft background not busy

f. Electronic Newsletter: logo, header and sidebar; simple and soft background not busy

h. Business card: sophisticated and simple

Colors

We have in mind a preference for colors from the purple family, maybe lavender, so as to appeal to all genders and age groups. Though we are happy to go with a recommendation if you think otherwise.

We would like a look that is professional, airy, bright, fresh, futuristic, insightful, friendly.

Ethos of the brand

- experiencing opportunity and being fulfilled in a changing world
- services are facilitated through insights
- support provided through our product, services and tailored approach to coaching/partnerships (which includes private client match-making)
- we are service providers and passionate about quality and modern leadership skills at all stages in life.

The company name is "Bright Harbor Ventures” - our main message is helping people move to the next level - through investments, personal and professional growth.

Some of our messaging

1. International Leadership in a new world.

2. New technology;

3. Informed;

4. Positively Influential

5. Making a difference;

6. Empowered;

7. Risk free investments;

8. Commercial opportunity;

9. Fulfilled living;

10. Carefree and Fun Living;

11. Progression;

12. Open-minded

13. Energy/dynamic

The Business:
The business is to move people very quickly out of situations that hold them back. the situations could be their own personal situations; their career; their jobs; their teams; their ideas; their finances; their financial opportunities. Remove their fears and give them the strategies to take action. The team are international and have 40 years experience between them in this area.

We do want to come across modern and dynamic, customer outcome focussed, building long-term relationships; international.
Updates

Project Deadline Extended
Reason: We have not found the right designs - we are not just looking for a website design but also images and logos. Most images we can see in the designs are stock images - very standard. We need an image which will be the face of the company, like the shop front window. This main image will be used on social media (top image) and also the home page of the website.

Target Market(s)

30-55 years
Eastern Europe; UK; Asia; Africa; Middle East
Personal, Professional, Corporate, and Financial Growth

Industry/Entity Type

Business Service

Contact Information for Business Card

Simple and stylish
the 3 areas of the business on the reverse -

International look - Offices in UK and San Francisco

Company name
web address www.brightharborventure.com
email director@brightharborventure.com
Facebook bright harbor venture
LinkedIn Bright Harbor Venture
Twitter Bright Harbor Venture
Telephone: +44 (0) 768 213 5597

Logo Text

Something that symbolises unlimited growth - probably not text - could use the word INSIGHT in some way

Number of Pages Required

1 page

Colors
e4daeb
f3f1f8
ffffff

Requirements
Must have
• social media symbols and address
• company name
• Melanie Thorpe
• Director
• Telephone +44 (0) 768 213 5597
• Website name www.brightharborventure.co.uk
• Reverse of Card:
• Discreet, Fast, Bright Harbor Consultancy
• Corporate, Professional, Personal & Property Investment
Nice to have
• not too angular; soft lines; not too cluttered (possibly social media on the reverse and just logo, name, number on the front?
Should not have
• too busy

```html
<!DOCTYPE html>
<html lang="en">
<head>
<meta charset="utf-8">
<title>Bright Harbor Venture</title>
<link href="https://fonts.googleapis.com/css2?family=Open+Sans:wght@300;400;600;700&display=swap" rel="stylesheet">
<style>
:root{
  --ink:#333333;
  --muted:#6b6b6b;
  --lavender:#e4daeb;
  --lavender-soft:#f3f1f8;
  --white:#ffffff;
  --accent-red:#e8525a;
  --footer:#2a2a2a;
  --footer-text:#9a9a9a;
}
*{margin:0;padding:0;box-sizing:border-box}
html,body{width:1200px;height:3005px;overflow:hidden}
body{font-family:"Open Sans",Arial,sans-serif;color:var(--ink);background:var(--white);position:relative}
.abs{position:absolute}

/* header */
.site-header{position:absolute;left:0;top:0;width:1200px;height:132px;background:var(--white)}
.brand-dot{left:180px;top:14px;width:48px;height:48px;border-radius:50%;background:var(--lavender)}
.brand-name{left:100px;top:82px;font-size:25px;font-weight:400;color:var(--ink);letter-spacing:-0.4px;white-space:nowrap}
.top-contact{top:32px;font-size:12.5px;color:var(--ink);display:flex;align-items:center;gap:12px;white-space:nowrap}
.top-contact .ic{width:32px;height:32px;border-radius:50%;background:var(--lavender);display:flex;align-items:center;justify-content:center}
.main-nav{top:94px;font-size:13px;color:var(--ink);white-space:nowrap}

/* hero */
.hero{left:0;top:132px;width:1200px;height:502px;background:linear-gradient(180deg,#5e6877 0%,#3a4456 35%,#2a3346 60%,#4a3b36 85%,#2b2c33 100%)}
.hero-title{left:0;width:1200px;top:164px;text-align:center;color:var(--white);font-size:42px;font-weight:700;letter-spacing:0.5px}
.hero-sub{left:0;width:1200px;top:224px;text-align:center;color:var(--white);font-size:35px;font-weight:300;letter-spacing:0.3px}
.hero-btn{left:514px;top:294px;width:172px;height:48px;border:2px solid var(--white);color:var(--white);font-size:14.5px;font-weight:700;display:flex;align-items:center;justify-content:center}
.hero-arrow{top:230px;width:42px;height:42px;border:1.5px solid rgba(255,255,255,.7);border-radius:50%;display:flex;align-items:center;justify-content:center}

/* welcome */
.section-title{left:0;width:1200px;text-align:center;font-weight:700;color:var(--ink)}
.welcome-title{top:692px;font-size:22px}
.welcome-sub{left:0;width:1200px;text-align:center;top:730px;font-size:19px;color:var(--ink)}
.video-frame{left:100px;top:810px;width:446px;height:316px;background:#e2e2e2;padding:8px}
.video-frame .media{width:100%;height:100%;background:linear-gradient(135deg,#d9d6d2 0%,#8a8580 40%,#2d2f35 75%,#4a4c52 100%);position:relative}
.play-btn{position:absolute;left:180px;top:110px;width:80px;height:80px;border-radius:50%;background:var(--accent-red);display:flex;align-items:center;justify-content:center}
.welcome-copy{left:620px;top:816px;width:450px;font-size:11.5px;line-height:24px;color:var(--muted)}
.welcome-copy p{margin-bottom:13px}

/* services */
.services{left:0;top:1224px;width:1200px;height:432px;background:linear-gradient(90deg,#2b2d33 0%,#3d3e44 45%,#25262b 100%)}
.service{top:92px;width:300px;color:var(--white)}
.service svg{display:block;margin-bottom:24px}
.service h3{font-size:16.5px;font-weight:700;margin-bottom:14px;letter-spacing:0.2px}
.service ul{list-style:none;font-size:13px}
.service li{height:32px;display:flex;align-items:center;gap:12px}
.service li::before{content:"›";font-size:16px;line-height:1}

/* blog */
.blog-title{top:1722px;font-size:23px}
.blog-sub{left:0;width:1200px;text-align:center;top:1764px;font-size:12.5px;color:var(--muted)}
.post{top:1826px;width:270px}
.post h4{font-size:12.5px;font-weight:700;line-height:24px;color:var(--ink)}
.post .rule{width:44px;height:1px;background:#9a9a9a;margin:16px 0 14px}
.post p{font-size:12px;line-height:24px;color:var(--muted)}

/* clients */
.clients-title{top:2070px;font-size:22px}
.clients-sub{left:0;width:1200px;text-align:center;top:2116px;font-size:12px;line-height:24px;color:var(--muted)}
.testimonial{left:0;top:2212px;width:1200px;height:458px;background:linear-gradient(120deg,#2a1a16 0%,#5a3a2e 40%,#3a2620 70%,#1e1412 100%)}
.quote-mark{left:0;width:1200px;top:84px;text-align:center;color:var(--white);font-size:64px;font-weight:700;line-height:64px;font-family:Georgia,serif}
.quote-text{left:170px;width:860px;top:144px;text-align:center;color:var(--white);font-size:13.5px;line-height:27px}
.avatar{left:552px;top:226px;width:96px;height:96px;border-radius:50%;border:4px solid var(--white);background:linear-gradient(160deg,#d8c7b8,#8a7a70)}
.author{left:0;width:1200px;top:342px;text-align:center;color:var(--white);font-size:13px}
.dots{left:584px;top:388px;display:flex;gap:6px}
.dots span{width:6px;height:6px;border-radius:50%;background:rgba(255,255,255,.45)}
.dots span.on{background:var(--white)}

/* footer */
.site-footer{left:0;top:2670px;width:1200px;height:335px;background:var(--footer);color:var(--footer-text)}
.footer-head{top:46px;font-size:13px;font-weight:700;color:var(--white)}
.footer-text{font-size:11px;line-height:24px}
.footer-links{top:76px;list-style:none;font-size:11px;line-height:28px}
.social{display:flex;gap:6px}
.social span{width:28px;height:28px;border-radius:50%;background:#6a6a6a}
.footer-bottom{left:0;top:262px;width:1200px;border-top:1px solid #3a3a3a}
.copyright{left:0;width:1200px;top:296px;text-align:center;font-size:11px}
</style>
</head>
<body>

<header class="site-header">
  <div class="abs brand-dot"></div>
  <div class="abs brand-name">Bright harbor venture</div>
  <div class="abs top-contact" style="left:570px">
    <span class="ic"><svg width="16" height="16" viewBox="0 0 24 24"><path d="M6.6 10.8a15 15 0 0 0 6.6 6.6l2.2-2.2c.3-.3.7-.4 1-.2 1.1.4 2.3.6 3.6.6.6 0 1 .4 1 1V20c0 .6-.4 1-1 1A17 17 0 0 1 3 4c0-.6.4-1 1-1h3.5c.6 0 1 .4 1 1 0 1.3.2 2.5.6 3.6.1.3 0 .7-.2 1z" fill="#ffffff"/></svg></span>
    <span>Call Us : +44 (0) 768 213 5597</span>
  </div>
  <div class="abs top-contact" style="left:812px">
    <span class="ic"><svg width="16" height="16" viewBox="0 0 24 24"><rect x="3" y="6" width="18" height="12" rx="1" fill="#ffffff"/><path d="M3 6l9 7 9-7" stroke="#e4daeb" stroke-width="1.6" fill="none"/></svg></span>
    <span>Email Us : director@brightharborventure.com</span>
  </div>
  <nav>
    <span class="abs main-nav" style="left:400px">About You</span>
    <span class="abs main-nav" style="left:522px">About Us</span>
    <span class="abs main-nav" style="left:638px">Our Values</span>
    <span class="abs main-nav" style="left:762px">Testimonials</span>
    <span class="abs main-nav" style="left:898px">Social Media</span>
    <span class="abs main-nav" style="left:1034px">News Alert</span>
  </nav>
</header>

<section class="abs hero" role="img" aria-label="Aerial city view at dusk over a river and bridge">
  <div class="abs hero-title">BRIGHT HARBOR VENTURE</div>
  <div class="abs hero-sub">WE ARE A CONSULTING COMPANY IN THE UK</div>
  <div class="abs hero-btn">CONTACT HERE!</div>
  <div class="abs hero-arrow" style="left:30px"><svg width="14" height="14" viewBox="0 0 14 14"><path d="M9 2L4 7l5 5" stroke="#fff" stroke-width="1.5" fill="none"/></svg></div>
  <div class="abs hero-arrow" style="left:1126px"><svg width="14" height="14" viewBox="0 0 14 14"><path d="M5 2l5 5-5 5" stroke="#fff" stroke-width="1.5" fill="none"/></svg></div>
</section>

<section class="welcome">
  <h1 class="abs section-title welcome-title">WELCOME TO BRIGHT HARBOR VENTURE</h1>
  <p class="abs welcome-sub">Hello and welcome to the company that works with you on your terms.</p>
  <div class="abs video-frame">
    <div class="media" role="img" aria-label="Presenter at a flip chart with a team around a meeting table">
      <div class="play-btn"><svg width="30" height="34" viewBox="0 0 30 34"><path d="M4 2l24 15L4 32z" fill="#ffffff"/></svg></div>
    </div>
  </div>
  <div class="abs welcome-copy">
    <p>If you seek an experienced and trusted partner to work with you on an assignment or simply want some strategies to move your personal or professional talents to the next level then you are in the right place.</p>
    <p>If you feel that the pace of change in business is so fast that to be an outstanding leader you should ensure you are brought up to speed regularly then you are in the right place.</p>
    <p>If you are hearing about the essential new leadership essentials and you are ready to hear how to adopt them into your life or business then you are at the right place.</p>
    <p>I am so convinced that you will be delighted with how fast you can make change happen.</p>
  </div>
</section>

<section class="abs services" role="img" aria-label="Business people shaking hands in an office">
  <div class="abs service" style="left:148px">
    <svg width="110" height="94" viewBox="0 0 110 94"><rect x="34" y="4" width="70" height="48" rx="8" fill="none" stroke="#e4daeb" stroke-width="4"/><rect x="2" y="22" width="72" height="50" rx="8" fill="#e4daeb"/><path d="M18 72l-4 18 18-18z" fill="#e4daeb"/><rect x="14" y="36" width="46" height="5" rx="2" fill="#3a3b41"/><rect x="14" y="50" width="34" height="5" rx="2" fill="#3a3b41"/></svg>
    <h3>CONSULTANCY</h3>
    <ul><li>Professional and Personal</li><li>Next Generation Leaders (16-30)</li><li>Consultation Options</li></ul>
  </div>
  <div class="abs service" style="left:472px">
    <svg width="90" height="94" viewBox="0 0 90 94"><rect x="6" y="10" width="62" height="80" rx="6" fill="none" stroke="#e4daeb" stroke-width="4"/><rect x="24" y="2" width="26" height="14" rx="3" fill="#e4daeb"/><path d="M18 34h36M18 48h28M18 62h20" stroke="#e4daeb" stroke-width="4"/><path d="M50 74l30-30 6 6-30 30-9 3z" fill="#e4daeb"/></svg>
    <h3>ON ASSIGNMENT</h3>
    <ul><li>Team Cohesion Strategy</li><li>Go To Market Strategy</li><li>Internationalisation Strategy</li></ul>
  </div>
  <div class="abs service" style="left:790px">
    <svg width="96" height="94" viewBox="0 0 96 94"><rect x="6" y="4" width="44" height="86" fill="none" stroke="#e4daeb" stroke-width="4"/><rect x="50" y="34" width="40" height="56" fill="none" stroke="#e4daeb" stroke-width="4"/><path d="M16 16h8M32 16h8M16 30h8M32 30h8M60 46h8M76 46h6M60 60h8M76 60h6" stroke="#e4daeb" stroke-width="4"/><ellipse cx="26" cy="66" rx="9" ry="12" fill="#e4daeb"/><path d="M26 74v16" stroke="#e4daeb" stroke-width="4"/></svg>
    <h3>PROPERTY: PRIVATE CLIENT</h3>
    <ul><li>Promotion and cash-buyer matching</li><li>Investment: high return projects</li><li>Commercial: Hotels and Senior Housing</li><li>Prestige Residential: US, Australia, UK</li></ul>
  </div>
</section>

<section class="blog">
  <h2 class="abs section-title blog-title">BLOG POSTS</h2>
  <p class="abs blog-sub">Lorem Ipsum is simply dummy text of the printing and typesetting industry. Lorem Ipsum has been the industry</p>
  <article class="abs post" style="left:100px"><h4>LOREM IPSUM IS SIMPLY DUMMY TEXT<br>OF THE PRINTING</h4><div class="rule"></div><p>Lorem Ipsum is simply dummy text of the printing and typesetting industry. Lorem Ipsum has been the industry's standard dummy text ever since the 1500s</p></article>
  <article class="abs post" style="left:468px"><h4>LOREM IPSUM IS SIMPLY DUMMY TEXT<br>OF THE PRINTING</h4><div class="rule"></div><p>Lorem Ipsum is simply dummy text of the printing and typesetting industry. Lorem Ipsum has been the industry's standard dummy text ever since the 1500s</p></article>
  <article class="abs post" style="left:836px"><h4>LOREM IPSUM IS SIMPLY DUMMY TEXT<br>OF THE PRINTING</h4><div class="rule"></div><p>Lorem Ipsum is simply dummy text of the printing and typesetting industry. Lorem Ipsum has been the industry's standard dummy text ever since the 1500s</p></article>
</section>

<section class="clients">
  <h2 class="abs section-title clients-title">WHAT OUR CLIENT’S SAY</h2>
  <p class="abs clients-sub">Lorem Ipsum es simplemente el texto de relleno de las imprentas y archivos de texto. Lorem Ipsum ha sido el texto de<br>relleno estándar de las industrias</p>
</section>

<section class="abs testimonial" role="img" aria-label="Hands holding a tablet in warm light">
  <div class="abs quote-mark">“</div>
  <p class="abs quote-text">Lorem Ipsum is simply dummy text of the printing and typesetting industry. Lorem Ipsum has been the industry's standard dummy text ever since the 1500s, when an unknown printer took a galley of type and scrambled it to make a type specimen book</p>
  <div class="abs avatar" role="img" aria-label="Portrait of the client"></div>
  <p class="abs author"><b>- Marcus Ellwood -</b> Business man</p>
  <div class="abs dots"><span class="on"></span><span></span><span></span></div>
</section>

<footer class="abs site-footer">
  <div class="abs footer-head" style="left:102px">COMPANY</div>
  <p class="abs footer-text" style="left:102px;top:76px;width:340px">Company: Bright Harbor Venture Limited, registered in England and Wales.<br><b style="color:#d0d0d0">Registeres number 48211590.</b></p>
  <div class="abs social" style="left:102px;top:172px"><span></span><span></span><span></span><span></span><span></span></div>

  <div class="abs footer-head" style="left:512px">WELCOME</div>
  <ul class="abs footer-links" style="left:512px"><li>About You</li><li>About Us</li><li>Our Values</li><li>Testimonials</li><li>Social Media</li><li>News Alert</li></ul>

  <div class="abs footer-head" style="left:684px">INFORMATION</div>
  <ul class="abs footer-links" style="left:684px"><li>Terms &amp; Conditions</li><li>Privacy policy</li><li>Disclaimer</li><li>Contact us</li><li>Sitemap</li></ul>

  <div class="abs footer-head" style="left:876px">CONTACT INFO</div>
  <p class="abs footer-text" style="left:876px;top:76px;width:230px;line-height:22px">Let's chat, if you want a non committal conversation get in touch by email or telephone.</p>
  <p class="abs footer-text" style="left:876px;top:154px;display:flex;align-items:center;gap:10px;white-space:nowrap"><svg width="12" height="10" viewBox="0 0 12 10"><rect width="12" height="10" fill="#bdbdbd"/><path d="M0 0l6 5 6-5" stroke="#2a2a2a" fill="none"/></svg>Email: director@brightharborventure.com</p>
  <p class="abs footer-text" style="left:876px;top:182px;display:flex;align-items:center;gap:10px;white-space:nowrap"><svg width="12" height="12" viewBox="0 0 24 24"><path d="M6.6 10.8a15 15 0 0 0 6.6 6.6l2.2-2.2c.3-.3.7-.4 1-.2 1.1.4 2.3.6 3.6.6.6 0 1 .4 1 1V20c0 .6-.4 1-1 1A17 17 0 0 1 3 4c0-.6.4-1 1-1h3.5c.6 0 1 .4 1 1 0 1.3.2 2.5.6 3.6.1.3 0 .7-.2 1z" fill="#bdbdbd"/></svg>Call: +44 (0) 768 213 5597</p>

  <div class="abs footer-bottom"></div>
  <p class="abs copyright">© 2016, Bright harbor venture. All rights reserved</p>
</footer>

</body>
</html>
```